Business Card Design

Lark Haven Rentals
Lark Haven Rentals is a high end home rental leasing company that provides exquisite properties in niche markets. We are a small family owned business that considers our clients not as renters, but as friends. Every property we buy must be brought up to our high standards before it is offered on the market. The properties that we lease are exceptional, "move in" ready homes. This allows for the client to take pride in their lease as if it was their own home. To put it another way; we do not lease a property that we would not live in ourselves.

Target Market(s)

Couples making $100K or more

Industry/Entity Type

Business

Requirements
Must have
• Some sort of logo
Nice to have
• good slogan
Should not have
• Pink

```html
<!DOCTYPE html>
<html lang="en">
<head>
<meta charset="utf-8">
<title>Lark Haven Rentals – Business Card</title>
<link href="https://fonts.googleapis.com/css2?family=Cinzel:wght@600&family=Ubuntu:wght@400;500;700&display=swap" rel="stylesheet">
<style>
  :root {
    --maroon: #7a2a1e;
    --paper: #ffffff;
    --backdrop: #d9dde2;
    --accent-green: #2e8b57;
  }
  html, body {
    margin: 0;
    padding: 0;
    width: 1200px;
    height: 1000px;
    overflow: hidden;
    background: var(--backdrop);
  }
  .card {
    position: absolute;
    left: 100px;
    top: 214px;
    width: 1000px;
    height: 572px;
    background: var(--paper);
    box-shadow: 0 6px 18px rgba(0,0,0,0.18);
    overflow: hidden;
  }
  .contact-panel {
    position: absolute;
    left: 0;
    top: 0;
    width: 460px;
    height: 100%;
    background: var(--maroon);
    color: var(--paper);
    font-family: 'Ubuntu', sans-serif;
  }
  .contact-panel .divider {
    position: absolute;
    left: 0;
    right: 0;
    top: 480px;
    height: 9px;
    background: var(--paper);
  }
  .person {
    position: absolute;
    left: 58px;
    top: 92px;
    width: 200px;
  }
  .person .name {
    font-weight: 700;
    font-size: 34px;
    line-height: 1;
    margin: 0;
    white-space: nowrap;
  }
  .person .title {
    font-size: 20px;
    text-align: right;
    margin: 4px 0 0;
  }
  .contact-list {
    position: absolute;
    left: 64px;
    top: 362px;
    margin: 0;
    padding: 0;
    list-style: none;
    font-size: 24px;
    font-weight: 500;
    line-height: 1.35;
  }
  .company-heading {
    position: absolute;
    left: 510px;
    top: 64px;
    margin: 0;
    font-family: 'Cinzel', serif;
    font-weight: 600;
    font-size: 30px;
    color: var(--maroon);
    letter-spacing: 1px;
  }
  .brand-lockup {
    position: absolute;
    left: 560px;
    top: 255px;
    display: flex;
    align-items: center;
    gap: 16px;
  }
  .brand-lockup .mark {
    width: 34px;
    height: 34px;
    background: var(--accent-green);
  }
  .brand-lockup .brand-name {
    font-family: 'Cinzel', serif;
    font-weight: 600;
    font-size: 34px;
    color: var(--maroon);
    white-space: nowrap;
  }
  .brand-rule {
    position: absolute;
    left: 478px;
    right: 0;
    top: 352px;
    height: 8px;
    background: var(--maroon);
  }
</style>
</head>
<body>
  <div class="card">
    <section class="contact-panel">
      <div class="person">
        <p class="name">Your Name</p>
        <p class="title">Title</p>
      </div>
      <ul class="contact-list">
        <li>Phone : 123- 456-7890</li>
        <li>E-mail : yourname@mail.com</li>
        <li>Website : www.address.com</li>
      </ul>
      <div class="divider"></div>
    </section>

    <h1 class="company-heading">Lark Haven Rentals</h1>

    <div class="brand-lockup">
      <span class="mark"></span>
      <span class="brand-name">Lark Haven Rentals</span>
    </div>
    <div class="brand-rule"></div>
  </div>
</body>
</html>
```